Velvet Lantern rebranding my business with a new business card

I have my new logo and now I need a refresher on my business cards. I really want something fun and fresh. I like black background or anything to make the color pop.
Logo
Name: Velvet Lantern
Contact Info as stated below:
Mira Pellow
555-013-4762
Logo
Name: Velvet Lantern
Mira Pellow
555-013-4762
fb.me/VelvetLanternbyMira
Instagram: @VelvetLanternbyMira

Industry/Entity Type

Business

Contact Information for Business Card

double-sided. Logo on one side. Contact info on the other.

Requirements
Must have
• Logo
• Name: Velvet Lantern
• Contact Info as stated below:
• Mira Pellow
• 555-013-4762
• fb.me/VelvetLanternbyMira
• fb.me/VelvetLanternbyMira

```html
<!DOCTYPE html>
<html lang="en">
<head>
<meta charset="utf-8">
<title>Velvet Lantern – Business Card</title>
<link rel="stylesheet" href="https://fonts.googleapis.com/css2?family=Raleway:wght@400;500;600&display=swap">
<style>
  :root {
    --stage: #101010;
    --card-white: #ffffff;
    --card-dark: #1d1d1f;
    --card-dark-edge: #262628;
    --pink: #e48cbf;
    --pink-soft: #f2b9d7;
    --teal: #8fd3c8;
    --ink: #1b1b1b;
    --ghost: rgba(255, 255, 255, 0.07);
  }
  * { box-sizing: border-box; margin: 0; padding: 0; }
  html, body {
    width: 1200px; height: 1000px; overflow: hidden;
    background: var(--stage);
    font-family: "Raleway", sans-serif;
  }
  .stage { position: relative; width: 1200px; height: 1000px; }

  .card {
    position: absolute;
    width: 520px; height: 320px;
    border-radius: 22px;
    overflow: hidden;
    box-shadow: 0 18px 40px rgba(0, 0, 0, 0.55);
  }

  /* Front */
  .card--front { left: 70px; top: 230px; background: var(--card-white); }
  .card--front .waves { position: absolute; inset: 0; }
  .brand-seal {
    position: absolute; left: 50%; top: 50%;
    width: 176px; height: 176px;
    transform: translate(-50%, -50%);
    border-radius: 50%;
    border: 3px solid var(--pink-soft);
    box-shadow: inset 0 0 0 6px var(--card-white), inset 0 0 0 7px var(--pink-soft);
    display: flex; align-items: center; justify-content: center;
    text-align: center;
  }
  .brand-name {
    font-family: "Raleway", sans-serif;
    font-weight: 600;
    font-size: 24px;
    line-height: 1.15;
    color: var(--pink);
  }

  /* Back */
  .card--back {
    left: 610px; top: 450px;
    background: linear-gradient(160deg, var(--card-dark-edge), var(--card-dark) 60%);
  }
  .holder-name {
    position: absolute; left: 36px; top: 34px;
    font-size: 34px; font-weight: 500; letter-spacing: 0.5px;
  }
  .holder-name .first { color: var(--teal); }
  .holder-name .last { color: var(--pink); }

  .brand-ghost {
    position: absolute;
    font-weight: 600; font-size: 30px;
    color: var(--ghost);
    white-space: nowrap;
  }
  .brand-ghost--left { left: 40px; top: 130px; }
  .brand-ghost--right { left: 290px; top: 120px; }

  .contact-band {
    position: absolute; right: 0;
    height: 36px;
    border-radius: 18px 0 0 18px;
    display: flex; align-items: center;
    padding-left: 6px; padding-right: 24px;
    font-size: 22px; font-weight: 500; color: var(--ink);
  }
  .contact-band--phone { top: 220px; width: 250px; background: var(--pink); }
  .contact-band--social { top: 262px; width: 330px; background: var(--teal); }
  .contact-icon {
    width: 26px; height: 26px; flex: none;
    border-radius: 50%;
    background: var(--card-dark);
    display: flex; align-items: center; justify-content: center;
    margin-right: 12px;
  }
</style>
</head>
<body>
<main class="stage">

  <section class="card card--front" aria-label="Business card front">
    <svg class="waves" width="520" height="320" viewBox="0 0 520 320" aria-hidden="true">
      <path d="M0 0 H360 C300 60 200 40 120 70 C70 88 30 100 0 110 Z" fill="var(--pink)"/>
      <path d="M520 160 C460 150 400 170 360 220 C320 270 240 290 150 320 H520 Z" fill="var(--teal)"/>
    </svg>
    <div class="brand-seal">
      <span class="brand-name">Velvet<br>Lantern</span>
    </div>
  </section>

  <section class="card card--back" aria-label="Business card back">
    <h1 class="holder-name"><span class="first">Mira</span> <span class="last">Pellow</span></h1>

    <span class="brand-ghost brand-ghost--left" aria-hidden="true">Velvet Lantern</span>
    <span class="brand-ghost brand-ghost--right" aria-hidden="true">Velvet Lantern</span>

    <div class="contact-band contact-band--phone">
      <span class="contact-icon">
        <svg width="14" height="14" viewBox="0 0 24 24" aria-hidden="true">
          <path d="M6.6 10.8a15 15 0 0 0 6.6 6.6l2.2-2.2a1 1 0 0 1 1-.25 11.4 11.4 0 0 0 3.6.57 1 1 0 0 1 1 1V20a1 1 0 0 1-1 1A17 17 0 0 1 3 4a1 1 0 0 1 1-1h3.5a1 1 0 0 1 1 1c0 1.25.2 2.45.57 3.57a1 1 0 0 1-.25 1z" fill="var(--pink)"/>
        </svg>
      </span>
      555-013-4762
    </div>
    <div class="contact-band contact-band--social">
      <span class="contact-icon"></span>
      VelvetLanternbyMira
    </div>
  </section>

</main>
</body>
</html>
```